Start up Dialysis Clinic needs its first website - Velmira Health

Create a visually appealing and user-friendly website for Velmira Health, a dialysis clinic located in Mt. Irvine, Tobago. The website should effectively communicate our services to local, regional, and international patients, providing essential information and fostering trust and engagement..
Key Goals:

1. Informative: Provide comprehensive information about our services, facility, and team.
2. User-Friendly: Ensure the website is easy to navigate, with a clear structure and accessible content.
3. Engaging: Create a visually appealing design that reflects the professionalism and care of Velmira Health.
4. Responsive: Ensure the website is fully responsive and performs well on all devices, including desktops, tablets, and smartphones.
5. Trust-Building: Include testimonials, credentials, and patient resources to build trust with potential patients.
Scope of Work:

1. Home Page: An inviting and informative landing page that provides an overview of our clinic, mission, and services. Include a call to action for more information and contact details.
2. About Us: A detailed page about Velmira Health, including our mission, vision, team, and facility tour.
3. Services: A comprehensive page describing the dialysis services we offer, including Hemodialysis, Peritoneal Dialysis, and Home Hemodialysis.
4. Patient Information: A resourceful section with guides for new patients, FAQs, insurance and billing information, and downloadable forms.
5. Resources: Educational content about kidney health, dialysis options, diet and nutrition tips, and support groups.
6. Contact Us: A contact page with our address, phone number, email, office hours, a contact form, and a map.

```html
<!DOCTYPE html>
<html lang="en">
<head>
<meta charset="utf-8">
<title>Velmira Health – Dialysis Clinic</title>
<link href="https://fonts.googleapis.com/css2?family=Exo+2:wght@600;700&family=Lato:wght@400;700&display=swap" rel="stylesheet">
<style>
:root{
  --blue:#3f72b8;
  --blue-dark:#34609e;
  --green:#6a9f48;
  --green-dark:#5b8e3d;
  --ink:#333a44;
  --muted:#555c66;
  --hero-bg:#edf2fa;
  --card-line:#e6e9ee;
  --footer:#000;
  --white:#fff;
}
*{box-sizing:border-box;margin:0;padding:0}
html,body{width:1200px;height:3530px;overflow:hidden}
body{position:relative;font-family:'Lato',sans-serif;color:var(--ink);background:var(--white)}
.abs{position:absolute}
.heading{font-family:'Exo 2',sans-serif;font-weight:700}
.btn{position:absolute;display:flex;align-items:center;justify-content:center;background:var(--green);color:var(--white);font-size:15px;border-radius:3px}
.ph{position:absolute}

/* header */
.brand{position:absolute;display:flex;flex-direction:column;align-items:center;color:var(--blue);font-family:'Exo 2',sans-serif;font-weight:700;line-height:1;white-space:nowrap}
.brand .mark{background:var(--green)}
.brand-top{left:112px;top:14px;width:131px;gap:14px;font-size:21px}
.brand-top .mark{width:50px;height:50px}
.contact{display:flex;align-items:center;gap:16px}
.contact .ico{width:60px;height:60px;border-radius:50%;background:linear-gradient(135deg,var(--blue),var(--green));display:flex;align-items:center;justify-content:center;flex:none}
.contact .lbl{color:var(--blue);font-size:16px}
.contact .val{font-size:17px;color:var(--ink);margin-top:4px;white-space:nowrap}

.nav{left:111px;top:129px;width:978px;height:76px;background:var(--green);border-radius:4px;display:flex;align-items:center;padding-left:41px;z-index:3}
.nav a{color:var(--white);font-size:15px;text-decoration:none;margin-right:64px}
.nav a.active{background:var(--white);color:var(--blue);padding:8px 10px;margin-right:52px}

/* hero */
.hero{left:0;top:160px;width:1200px;height:600px;background:var(--hero-bg);overflow:hidden}
.hero-copy{left:112px}
.section-title{position:absolute;left:0;width:1200px;text-align:center;font-size:44px;letter-spacing:.5px}
.section-title .b{color:var(--blue)} .section-title .g{color:var(--green)}

/* cards */
.svc{position:absolute;top:929px;width:312px;height:368px;background:var(--white);border-radius:8px;box-shadow:0 2px 10px rgba(0,0,0,.08);overflow:hidden}
.svc .img{position:absolute;left:0;top:0;width:312px;height:225px}
.svc .pill{position:absolute;left:0;top:207px;height:36px;padding:0 18px;background:var(--green);color:var(--white);font-size:15px;display:flex;align-items:center;border-radius:0 18px 18px 0}
.svc h3{position:absolute;left:24px;top:258px;font-family:'Exo 2',sans-serif;font-weight:600;font-size:21px;color:var(--blue)}
.svc p{position:absolute;left:24px;top:290px;width:272px;font-size:13px;line-height:20px;color:var(--muted)}

.testi{position:absolute;top:2388px;width:312px;height:360px;background:var(--white);box-shadow:0 2px 12px rgba(0,0,0,.09);border-bottom:5px solid var(--green);text-align:center}
.testi .av{position:absolute;left:113px;top:29px;width:86px;height:86px;border-radius:50%}
.testi h4{position:absolute;top:130px;width:100%;font-family:'Exo 2',sans-serif;font-weight:600;font-size:23px;color:var(--blue)}
.testi p{position:absolute;top:178px;left:18px;width:276px;font-size:15px;line-height:22px;color:var(--muted)}
.testi .sub{position:absolute;top:282px;width:100%;color:var(--green);font-size:16px}
.testi .stars{position:absolute;top:312px;width:100%;color:#f4c20d;font-size:18px;letter-spacing:2px}

/* footer */
.footer{left:0;top:2876px;width:1200px;height:599px;background:var(--footer);color:var(--white)}
.brand-foot{left:112px;top:38px;width:180px;gap:16px;font-size:27px}
.brand-foot .mark{width:76px;height:76px}
.fcol h5{font-family:'Exo 2',sans-serif;font-weight:600;font-size:20px}
.fcol .rule{width:86px;height:2px;background:linear-gradient(90deg,transparent,var(--green));margin-top:10px;margin-bottom:18px}
.fcol ul{list-style:none}
.fcol li{font-size:15px;height:36px;display:flex;align-items:flex-start;gap:14px}
.fcol li::before{content:"›";color:var(--green);font-size:18px;line-height:16px}
.social{width:38px;height:38px;background:var(--green);border-radius:3px;display:flex;align-items:center;justify-content:center}
.post{display:flex;gap:12px;margin-bottom:30px}
.post .th{width:68px;height:67px;background:linear-gradient(135deg,#bcd3ea,#8fa9c7);flex:none}
.post b{font-size:15px;line-height:22px;display:block;width:150px}
.post small{font-size:12px;display:block;margin-top:6px}
.post small::before{content:"";display:inline-block;width:8px;height:8px;background:var(--green);margin-right:6px}
.copy{left:0;top:3475px;width:1200px;height:55px;background:var(--blue);color:var(--white);font-size:14px;display:flex;align-items:center;justify-content:center}
</style>
</head>
<body>

<!-- Header -->
<div class="brand brand-top"><span class="mark"></span>Velmira Health</div>

<div class="abs contact" style="left:340px;top:35px">
  <div class="ico"><svg width="24" height="24" viewBox="0 0 24 24"><path fill="#fff" d="M6.6 10.8a15 15 0 0 0 6.6 6.6l2.2-2.2c.3-.3.7-.4 1-.2 1.1.4 2.3.6 3.6.6.6 0 1 .4 1 1V20c0 .6-.4 1-1 1C10.6 21 3 13.4 3 4c0-.6.4-1 1-1h3.5c.6 0 1 .4 1 1 0 1.3.2 2.5.6 3.6.1.3 0 .7-.2 1z"/></svg></div>
  <div><div class="lbl">Call Us</div><div class="val">+1 868 555 0142</div></div>
</div>
<div class="abs contact" style="left:597px;top:35px">
  <div class="ico"><svg width="24" height="20" viewBox="0 0 24 20"><rect x="1" y="2" width="22" height="16" rx="2" fill="#fff"/><path d="M2 4l10 7 10-7" stroke="#5b86b5" stroke-width="2" fill="none"/></svg></div>
  <div><div class="lbl">Email</div><div class="val">info@velmirahealth.com</div></div>
</div>
<div class="btn" style="left:916px;top:45px;width:172px;height:38px;font-size:14px">Make Appointment</div>

<!-- Hero -->
<div class="abs hero">
  <svg class="abs" style="left:0;top:0" width="1200" height="600"><polygon points="505,0 1200,0 1200,600 640,600" fill="#5b86c6"/></svg>
  <div class="ph" style="left:585px;top:100px;width:420px;height:437px;background:var(--white)"></div>
  <div class="ph" role="img" aria-label="Smiling male doctor in a white coat with a stethoscope, arms crossed" style="left:600px;top:115px;width:390px;height:407px;background:linear-gradient(160deg,#6f96d0,#4d79bb)"></div>
  <div class="ph" role="img" aria-label="Doctor figure continuing below the frame" style="left:620px;top:522px;width:300px;height:78px;background:linear-gradient(180deg,#dfe5ee,#c8d2df)"></div>

  <div class="abs hero-copy" style="top:135px;font-size:27px;color:var(--ink)">Welcome To</div>
  <div class="abs hero-copy heading" style="top:178px;font-size:84px;color:var(--blue);line-height:1">VELMIRA</div>
  <div class="abs hero-copy heading" style="top:280px;font-size:64px;color:var(--green);line-height:1">HEALTH</div>
  <p class="abs hero-copy" style="top:362px;width:400px;font-size:17px;line-height:24px;color:var(--muted)">Lorem ipsum dolor sit amet, consectetur adipiscing elit, sed do eiusmod tempor ncididunt ut labore et dolore magna aliqua.</p>
  <div class="btn" style="left:112px;top:462px;width:171px;height:38px">Make Appointment</div>
</div>

<!-- Nav -->
<nav class="abs nav">
  <a class="active">Home</a><a>About Us</a><a>Services</a><a>Resources</a><a>Patient Information</a><a>Contact Us</a>
  <svg style="position:absolute;right:42px;top:24px" width="28" height="28" viewBox="0 0 28 28"><circle cx="12" cy="12" r="9" stroke="#fff" stroke-width="2.5" fill="none"/><path d="M19 19l7 7" stroke="#fff" stroke-width="2.5"/></svg>
</nav>

<!-- Services -->
<h2 class="section-title heading" style="top:836px"><span class="b">OUR</span> <span class="g">SERVICES</span></h2>

<div class="svc" style="left:111px">
  <div class="img" role="img" aria-label="Patient setting up peritoneal dialysis at home" style="background:linear-gradient(135deg,#b8a58a,#7d6f63)"></div>
  <div class="pill">Read More</div>
  <h3>Peritoneal Dialysis</h3>
  <p>Excepteur sint occaecat cupidatat non proident, sunt in culpa qui officia deserunt mollit anim id est laborum.</p>
</div>
<div class="svc" style="left:444px">
  <div class="img" role="img" aria-label="Hemodialysis machine in a treatment room" style="background:linear-gradient(135deg,#c9d4e0,#8796aa)"></div>
  <div class="pill">Read More</div>
  <h3>Including Hemodialysis</h3>
  <p>Excepteur sint occaecat cupidatat non proident, sunt in culpa qui officia deserunt mollit anim id est laborum.</p>
</div>
<div class="svc" style="left:776px">
  <div class="img" role="img" aria-label="Nurse in scrubs beside patients in a dialysis ward" style="background:linear-gradient(135deg,#d8dde2,#8fa7bd)"></div>
  <div class="pill">Read More</div>
  <h3>Home Hemodialysis</h3>
  <p>Excepteur sint occaecat cupidatat non proident, sunt in culpa qui officia deserunt mollit anim id est laborum.</p>
</div>

<!-- Clinic -->
<div class="ph" role="img" aria-label="Doctor talking with an elderly patient in the clinic" style="left:111px;top:1385px;width:346px;height:371px;border-radius:14px;background:linear-gradient(135deg,#c9d8c8,#8a96a3)"></div>
<div class="ph" style="left:357px;top:1548px;width:193px;height:174px;background:var(--blue);border-radius:44px 0 0 0;border-left:6px solid #fff;border-top:6px solid #fff;color:#fff">
  <div style="position:absolute;left:20px;top:32px;font-size:42px;font-family:'Exo 2',sans-serif">25</div>
  <div style="position:absolute;left:96px;top:30px;width:58px;height:58px;background:#fff;border-radius:3px"></div>
  <div style="position:absolute;left:16px;top:108px;font-size:19px;white-space:nowrap">years experience</div>
</div>
<h2 class="abs heading" style="left:606px;top:1374px;font-size:44px"><span style="color:var(--blue)">OUR</span> <span style="color:var(--green)">CLINIC</span></h2>
<p class="abs" style="left:606px;top:1455px;width:470px;font-size:15px;line-height:24px;color:var(--muted)">Sed ut perspiciatis unde omnis iste natus error sit voluptatem accusan tium doloremque laudantium, totam rem aperiam, eaque ipsa quae ab illo inventore veritatis et quasi architecto beatae vitae dicta sunt expli cabo. Nemo enim ipsam voluptatem quia voluptas sit aspernatur aut odit aut fugit, sed quia consequuntur magni dolores eos qui ratione vo luptatem sequi nesciunt. orem ipsum dolor sit amet, consectetur adipi scing elit, sed do eiusmod tempor incididunt ut labore et dolore magna aliqua. Ut enim ad minim veniam, quis nostrud exercitation ullamco laboris nisi ut aliquip ex ea commodo consequat</p>
<div class="btn" style="left:606px;top:1717px;width:155px;height:38px">Read More</div>

<!-- Mission -->
<div class="ph" style="left:111px;top:1844px;width:977px;height:386px;border-radius:14px;background:linear-gradient(120deg,#3f72b8 0%,#4d80b0 45%,#6aa24a 100%)"></div>
<div class="ph" role="img" aria-label="Smiling female doctor in a white coat pointing upward" style="left:750px;top:1715px;width:275px;height:515px;border-radius:120px 120px 0 0;background:linear-gradient(180deg,#e6d2c2 0%,#f2f3f5 35%,#dfe4ea 100%)"></div>
<h2 class="abs heading" style="left:158px;top:1888px;font-size:42px;color:#fff;word-spacing:8px">OUR MISSION</h2>
<p class="abs" style="left:158px;top:1966px;width:520px;font-size:15px;line-height:23px;color:#fff">Neque porro quisquam est, qui dolorem ipsum quia dolor sit amet, consecte-tur, adipisci velit, sed quia non numquam eius modi tempora incidunt ut labore et dolore magnam aliquam quaerat voluptatem. Ut enim ad minima veniam, quis nostrum exercitationem sed ut perspiciatis unde omnis iste natus error sit voluptatem accusantium ullam corporis suscipit laboriosam, nisi ut aliquid ex ea commodi consequatur.</p>
<div class="btn" style="left:158px;top:2144px;width:154px;height:38px;background:#fff;color:var(--blue)">Read More</div>

<!-- Testimonials -->
<h2 class="section-title heading" style="top:2305px"><span class="b">OUR</span> <span class="g">TESTIMONIALS</span></h2>

<div class="testi" style="left:111px">
  <div class="av" role="img" aria-label="Portrait of a patient" style="background:#f2b98e"></div>
  <h4>Lorem Ipsum</h4>
  <p>Lorem ipsum dolor sit amet, consectetur adipiscing elit, sed do eiusmod tempor incididunt ut labore et dolore magna aliqua. Quis ipsum ultrices gravida.</p>
  <div class="sub">Sed ut perspiciatis</div><div class="stars">★★★★★</div>
</div>
<div class="testi" style="left:444px">
  <div class="av" role="img" aria-label="Portrait of a patient" style="background:#9a9a9a"></div>
  <h4>Lorem Ipsum</h4>
  <p>Lorem ipsum dolor sit amet, consectetur adipiscing elit, sed do eiusmod tempor incididunt ut labore et dolore magna aliqua. Quis ipsum ultrices gravida.</p>
  <div class="sub">Sed ut perspiciatis</div><div class="stars">★★★★★</div>
</div>
<div class="testi" style="left:777px">
  <div class="av" role="img" aria-label="Portrait of a patient" style="background:#c9d2dc"></div>
  <h4>Lorem Ipsum</h4>
  <p>Lorem ipsum dolor sit amet, consectetur adipiscing elit, sed do eiusmod tempor incididunt ut labore et dolore magna aliqua. Quis ipsum ultrices gravida.</p>
  <div class="sub">Sed ut perspiciatis</div><div class="stars">★★★★★</div>
</div>
<svg class="abs" style="left:570px;top:2776px" width="60" height="12"><circle cx="6" cy="6" r="5" fill="#3f72b8"/><circle cx="22" cy="6" r="5" fill="#b9bec6"/><circle cx="38" cy="6" r="5" fill="#b9bec6"/><circle cx="54" cy="6" r="5" fill="#b9bec6"/></svg>

<!-- Footer -->
<footer class="abs footer">
  <div class="brand brand-foot"><span class="mark"></span>Velmira Health</div>
  <div class="abs" style="left:338px;top:48px;width:1px;height:118px;background:#444"></div>
  <div class="abs heading" style="left:381px;top:64px;font-size:29px;color:var(--blue);white-space:nowrap">News Subscription</div>
  <div class="abs" style="left:382px;top:108px;width:240px;font-size:12px;line-height:17px">Get Latest Deals from Velmira's Inbox &amp; Subscribe Now</div>
  <div class="abs" style="left:715px;top:84px;width:240px;height:45px;border:1px solid #bbb;border-radius:4px;font-size:12px;display:flex;align-items:center;padding-left:18px">Email Address
    <svg style="position:absolute;right:16px;top:17px" width="13" height="10"><rect x=".5" y=".5" width="12" height="9" stroke="#6a9f48" fill="none"/><path d="M1 1l5.5 4L12 1" stroke="#6a9f48" fill="none"/></svg></div>
  <div class="btn" style="left:966px;top:84px;width:123px;height:45px">Subscribe</div>
  <div class="abs" style="left:111px;top:217px;width:978px;height:1px;background:#333"></div>

  <div class="abs fcol" style="left:112px;top:276px;width:235px">
    <h5>About Company</h5><div class="rule"></div>
    <p style="font-size:15px;line-height:22px">Lorem ipsum dolor sit amet, consectetur adipiscing elit, sed do eiusmod tempor incididunt ut labore et dolore magna aliqua. Quis ipsum suspendisse ultrices gravida.</p>
    <div style="display:flex;gap:10px;margin-top:26px">
      <div class="social"><svg width="16" height="16"><rect x="4" y="2" width="8" height="12" fill="none" stroke="#fff" stroke-width="2"/></svg></div>
      <div class="social"><svg width="16" height="16"><circle cx="8" cy="8" r="6" fill="none" stroke="#fff" stroke-width="2"/></svg></div>
      <div class="social"><svg width="16" height="16"><rect x="2" y="2" width="12" height="12" rx="3" fill="none" stroke="#fff" stroke-width="2"/></svg></div>
    </div>
  </div>
  <div class="abs fcol" style="left:396px;top:276px">
    <h5>Quick Links</h5><div class="rule"></div>
    <ul><li>Home</li><li>About Us</li><li>Services</li><li>Resources</li><li>Patient Information</li><li>Contact Us</li></ul>
  </div>
  <div class="abs fcol" style="left:613px;top:276px">
    <h5>Quick Links</h5><div class="rule"></div>
    <ul><li>Terms &amp; Conditions</li><li>Privacy Policy</li><li>Cookies Policy</li><li>Help</li><li>Support</li><li>Faqs</li></ul>
  </div>
  <div class="abs fcol" style="left:858px;top:276px">
    <h5>Recent Posts</h5><div class="rule"></div>
    <div class="post"><div class="th" role="img" aria-label="Nurse caring for an elderly patient"></div><div><b>Lorem ipsum dolor sit amet, consectetur</b><small>July 26 2024</small></div></div>
    <div class="post"><div class="th" role="img" aria-label="Doctor consulting with a patient"></div><div><b>Lorem ipsum dolor sit amet, consectetur</b><small>July 26 2024</small></div></div>
  </div>
</footer>
<div class="abs copy">Copyright © 2024 Velmira Health. All rights reserved.</div>

</body>
</html>
```